Marlowby Services Website Design

We have most content but require a professional design. We have a logo already and will need it utilized along with several of the photos from the attached documentation.
First page should have our mission and Vision and the synapsis provided in the word document. Visitors will be prompted to select from one of our 3 divisions from this page.
Each division will have the same list of tabs : About, Services, Safety, Careers and Contact.
Photos on each divisions page should be representative of the divisions offerings. The word doc attached contains the requested content and we are open to edits that would complement and fill the website.
I like the Quorvane site www.quorvane.example - they are our competition so cant be modeled directly after this.
Please include prompts to request quote at each service page. align the format of the geotechnical page to the other 2 divisions.
I used chat gpt for some of the content so will need it optimized for SCO.

```html
<!DOCTYPE html>
<html lang="en">
<head>
<meta charset="utf-8">
<title>Marlowby Services</title>
<link href="https://fonts.googleapis.com/css2?family=Bebas+Neue&family=Rubik:wght@400;500;700&display=swap" rel="stylesheet">
<style>
:root{
  --red:#ee1c25;
  --black:#000;
  --white:#fff;
  --ivory:#f7f6f0;
  --grey:#6b6b6b;
  --muted:#8a8a8a;
  --photo-green:#6f8a4a;
  --photo-mud:#7c6e5e;
}
*{margin:0;padding:0;box-sizing:border-box}
html,body{width:1006px;height:1200px;overflow:hidden;background:var(--black)}
body{position:relative;font-family:"Rubik",sans-serif;color:var(--white)}
.display{font-family:"Bebas Neue",sans-serif;font-weight:400}
.brand{font-family:"Rubik",sans-serif;font-weight:700;letter-spacing:3px;text-transform:uppercase;position:absolute;line-height:1}

/* hero */
.hero-band{position:absolute;left:0;top:0;width:369px;height:426px;background:var(--red)}
.hero .brand{left:84px;top:21px;font-size:21px;color:var(--white)}
.hero-photo{position:absolute;left:84px;top:84px;width:405px;height:482px;
  background:linear-gradient(180deg,#5d7a3c 0%,var(--photo-green) 30%,#c9c9c4 45%,#8d8a80 62%,var(--photo-mud) 100%)}
.hero-texture{position:absolute;left:500px;top:0;width:506px;height:430px;
  background:radial-gradient(ellipse 70% 45% at 75% 20%,rgba(255,255,255,.07),rgba(255,255,255,0) 70%)}
.hero-title{position:absolute;left:512px;top:170px;font-size:98px;line-height:84px;color:var(--ivory)}
.scroll{position:absolute;left:511px;top:513px;font-size:10px;text-align:center}
.scroll span{display:block;font-size:14px;margin-top:4px}

/* mission */
.mission .brand{right:668px;top:609px;font-size:21px;color:var(--white)}
.mission-title{position:absolute;right:668px;top:662px;text-align:right;font-size:98px;line-height:84px;color:var(--ivory)}
.mission-copy{position:absolute;left:52px;top:834px;width:287px;text-align:right;font-size:13.4px;line-height:21px}

/* divisions */
.divisions{position:absolute;left:382px;top:566px;width:624px;height:565px;background:linear-gradient(180deg,var(--red),#e41d27)}
.divisions h2{position:absolute;left:0;right:0;top:64px;text-align:center;font-size:38px;line-height:1}
.divisions .lead{position:absolute;left:0;right:0;top:112px;text-align:center;font-size:9.3px}
.card{position:absolute;top:152px;width:169px;height:344px;background:var(--white);padding:14px 11px}
.card-photo{height:96px}
.card h3{margin-top:20px;font-size:19px;line-height:22px;color:#333}
.card p{margin-top:6px;font-size:9px;line-height:17px;color:var(--grey)}
.card .cta{position:absolute;left:11px;right:11px;bottom:24px;height:37px;background:var(--black);color:var(--white);
  font-size:8.5px;font-weight:500;display:flex;align-items:center;justify-content:center;box-shadow:0 6px 10px rgba(255,200,120,.35)}
.card.aerial{left:50px}.card.geo{left:231px}.card.renew{left:412px}
.aerial .card-photo{background:linear-gradient(180deg,#587a3e,#b9b6ad 55%,#7d7266)}
.geo .card-photo{background:linear-gradient(180deg,#3b78c6 0%,#9cbde0 50%,#8c7a5a 100%)}
.renew .card-photo{background:linear-gradient(160deg,#2a64c0,#4a8ad8)}
.renew .cta{right:15px}

/* footer */
.site-footer .brand{left:75px;top:1158px;font-size:21px;color:var(--red)}
.copyright{position:absolute;left:0;width:1006px;top:1163px;text-align:center;font-size:12.5px;color:var(--muted)}
.social{position:absolute;left:772px;top:1162px;display:flex;gap:10px;list-style:none}
.social li{font-size:9px;font-weight:500;color:var(--white)}
</style>
</head>
<body>
<section class="hero">
  <div class="hero-band"></div>
  <div class="brand">Marlowby</div>
  <div class="hero-texture" role="img" aria-label="Faint flowing line pattern"></div>
  <div class="hero-photo" role="img" aria-label="Aerial lift truck parked on a muddy site in front of trees"></div>
  <h1 class="hero-title display">Safety.<br>Quality.<br>Service.</h1>
  <div class="scroll">Scroll<span>↓</span></div>
</section>

<section class="mission">
  <div class="brand">Marlowby</div>
  <h2 class="mission-title display">Mission &amp;<br>Vision</h2>
  <p class="mission-copy">At Marlowby Services, we are dedicated to delivering unparalleled aerial access, geotechnical drilling, and service and maintenance solutions, consistently exceeding our clients' expectations. Our vision is to be the leading provider of aerial access, geotechnical drilling, and service solutions, setting the standard for excellence in safety, efficiency, and environmental stewardship.</p>
</section>

<section class="divisions">
  <h2 class="display">Select Division</h2>
  <p class="lead">Choose from one of our three specialized divisions to explore our services tailored to your industry needs:</p>
  <article class="card aerial">
    <div class="card-photo" role="img" aria-label="Aerial lift truck on a gravel site"></div>
    <h3 class="display">Aerial Access</h3>
    <p>Providing comprehensive aerial access solutions for efficient project execution.</p>
    <div class="cta">Elevate Your Projects</div>
  </article>
  <article class="card geo">
    <div class="card-photo" role="img" aria-label="Drilling rig beside a tall white tower"></div>
    <h3 class="display">Geotechnical<br>Drilling</h3>
    <p>Delivering advanced geotechnical drilling services to support ground investigations and analysis.</p>
    <div class="cta">Dig Deeper</div>
  </article>
  <article class="card renew">
    <div class="card-photo" role="img" aria-label="Wind turbine against a blue sky"></div>
    <h3 class="display">Renewable Energy<br>Services</h3>
    <p>Offering specialized services to support the renewable energy sector's infrastructure development.</p>
    <div class="cta">Power Your Future</div>
  </article>
</section>

<footer class="site-footer">
  <div class="brand">Marlowby</div>
  <p class="copyright">© 2024 by Marlowby Services Inc.</p>
  <ul class="social" aria-label="Social links"><li>Frendle</li><li>Chirpa</li><li>Linkory</li></ul>
</footer>
</body>
</html>
```